Business card design for Automotive workshop

We need a business card for a new automotive repair and tyre shop called Keelstone Prime Automotive located in New Zealand. We are a clean, modern and fresh workshop and company.

Front needs to feature logo,
my name:
Marlo Fenwicke (director)

Address:
48 Tarn Lane
Whitianga 3510

Phone: 07 594 2713
Mobile: 027 451 9362
Email: office@keelstoneautomotive.example.nz
Website: keelstoneautomotive.example.nz

Back needs to feature an area to write down appointment details, date and time.

Also feature a list of jobs and work we do such as,
Vehicle Servicing
All Mechanical Repairs
Warrant of Fitness
Tyres & Wheel Alignments
Automotive Diagnostics
Automotive Parts & Supplies

```html
<!DOCTYPE html>
<html lang="en">
<head>
<meta charset="utf-8">
<title>Keelstone Prime Automotive — Business Card</title>
<link rel="stylesheet" href="https://fonts.googleapis.com/css2?family=Roboto:wght@400;500;700&display=swap">
<style>
  :root {
    --backdrop: #3b3532;
    --card: #111111;
    --card-edge: #1c1c1c;
    --red: #d4202a;
    --silver: #d9d9d9;
    --grey: #a8a8a8;
    --field: #8e8e8e;
  }
  * { box-sizing: border-box; margin: 0; padding: 0; }
  html, body { width: 1200px; height: 844px; overflow: hidden; }
  body {
    background: var(--backdrop);
    font-family: "Roboto", Arial, sans-serif;
    position: relative;
  }
  .card {
    position: absolute;
    top: 267px;
    width: 540px;
    height: 310px;
    background: var(--card);
    border: 1px solid var(--card-edge);
    box-shadow: 0 14px 30px rgba(0,0,0,.45);
  }
  .card--front { left: 40px; }
  .card--back { left: 620px; }

  .wordmark {
    position: absolute;
    text-align: center;
    font-weight: 700;
    letter-spacing: 1px;
    line-height: 1.15;
  }
  .card--front .wordmark { top: 46px; left: 0; right: 0; color: var(--red); font-size: 24px; }
  .card--back .wordmark { top: 40px; left: 0; right: 0; color: var(--silver); font-size: 24px; }

  .address {
    position: absolute;
    top: 140px;
    right: 34px;
    color: var(--grey);
    font-size: 14px;
    line-height: 1.35;
  }
  .person { position: absolute; top: 140px; left: 34px; }
  .person__name { color: var(--red); font-size: 19px; font-weight: 700; letter-spacing: .5px; }
  .person__role { color: var(--grey); font-size: 14px; margin-top: 2px; }

  .contacts { position: absolute; left: 34px; top: 208px; list-style: none; }
  .contacts li {
    display: flex; align-items: center; gap: 8px;
    color: var(--grey); font-size: 14px; line-height: 21px;
  }
  .contacts svg { width: 12px; height: 12px; fill: var(--red); flex: none; }

  .services {
    position: absolute; top: 104px; list-style: none;
    color: var(--silver); font-size: 13px; line-height: 20px;
  }
  .services--left { left: 40px; }
  .services--right { left: 290px; }
  .services li::before {
    content: ""; display: inline-block; width: 6px; height: 6px;
    border-radius: 50%; background: var(--silver);
    margin-right: 8px; vertical-align: middle;
  }

  .appointment__title {
    position: absolute; top: 190px; left: 0; right: 0; text-align: center;
    color: var(--silver); font-size: 15px; font-weight: 700; letter-spacing: .5px;
  }
  .appointment__row {
    position: absolute; top: 226px; left: 40px; right: 40px;
    display: flex; justify-content: space-between;
  }
  .appointment__field { display: flex; align-items: center; gap: 10px; color: var(--silver); font-size: 15px; }
  .appointment__blank { width: 150px; height: 32px; border-radius: 16px; background: var(--field); }
</style>
</head>
<body>
  <section class="card card--front" aria-label="Business card front">
    <div class="wordmark">KEELSTONE PRIME AUTOMOTIVE</div>
    <div class="address">48 Tarn Lane<br>Whitianga 3510</div>
    <div class="person">
      <div class="person__name">MARLO FENWICKE</div>
      <div class="person__role">Director</div>
    </div>
    <ul class="contacts">
      <li><svg viewBox="0 0 12 12"><path d="M2 1h2.5l1 3-1.5 1a7 7 0 0 0 3 3l1-1.5 3 1V11A10 10 0 0 1 1 2z"/></svg>07 594 2713</li>
      <li><svg viewBox="0 0 12 12"><path d="M3 0h6v12H3zM4 1.5v8h4v-8z"/></svg>027 451 9362</li>
      <li><svg viewBox="0 0 12 12"><path d="M0 2h12v8H0zM1 3l5 4 5-4z"/></svg>office@keelstoneautomotive.example.nz</li>
      <li><svg viewBox="0 0 12 12"><circle cx="6" cy="6" r="6"/></svg>keelstoneautomotive.example.nz</li>
    </ul>
  </section>

  <section class="card card--back" aria-label="Business card back">
    <div class="wordmark">KEELSTONE PRIME AUTOMOTIVE</div>
    <ul class="services services--left">
      <li>Vehicle Servicing</li>
      <li>All Mechanical Repairs</li>
      <li>Warrant of Fitness</li>
    </ul>
    <ul class="services services--right">
      <li>Tyres &amp; Wheel Alignments</li>
      <li>Automotive Diagnostics</li>
      <li>Automotive Parts &amp; Supplies</li>
    </ul>
    <div class="appointment__title">NEXT APPOINTMENT</div>
    <div class="appointment__row">
      <div class="appointment__field">DATE <span class="appointment__blank"></span></div>
      <div class="appointment__field">TIME <span class="appointment__blank"></span></div>
    </div>
  </section>
</body>
</html>
```